Mattress sale flyer front and back

FLYER SIZE!! front and back!
4.25" X 5.5"
or
10.7cm X 13.9 cm

This flyer needs to show the prices
twin.....$99
full.......$159
queen...$199
king....$299

the phone number........(786)471-3926
the address ..........24315 sw 142st miami fl 33157
if possible a map would be appreciated

possible brands to include.......Dorvin, Kaplets, brule & nasher, quilmdown

ATTACHED IS OUR OLD FLYER WITH OUTDATED INFORMATION, I WOULD LIKE SOMETHING SIMILAR. JUST ADD A LITTLE PRICE LIST AND A MAP

***FRONT AND BACK PLEASE****

```html
<!DOCTYPE html>
<html lang="en">
<head>
<meta charset="utf-8">
<title>Bayline Mattress Outlet – Flyer Front and Back</title>
<link href="https://fonts.googleapis.com/css2?family=Oswald:wght@400;500;600&display=swap" rel="stylesheet">
<style>
  :root {
    --canvas: #eceef0;
    --paper: #ffffff;
    --yellow: #f2e61c;
    --blue: #0f3f8c;
    --navy: #0c2a5c;
    --slate: #4a4c50;
    --ink: #2b2b2b;
    --photo-light: #e9eef2;
    --photo-teal: #1c8aa0;
    --map-base: #e4e0d8;
    --map-road: #c9c3b8;
    --badge: #c9a642;
  }
  * { box-sizing: border-box; margin: 0; padding: 0; }
  html, body { width: 1200px; height: 700px; overflow: hidden; }
  body {
    background: var(--canvas);
    font-family: "Oswald", "Arial Narrow", sans-serif;
    position: relative;
  }
  .flyer {
    position: absolute;
    top: 147px;
    width: 304px;
    height: 425px;
    background: var(--paper);
    box-shadow: 0 2px 8px rgba(0,0,0,0.12);
    overflow: hidden;
  }
  .flyer--front { left: 322px; }
  .flyer--back { left: 638px; }

  .brand-band {
    position: absolute;
    left: 0; right: 0;
    background: var(--yellow);
    display: flex;
    align-items: center;
    justify-content: center;
    text-align: center;
  }
  .brand-name {
    font-weight: 500;
    color: var(--ink);
    letter-spacing: 1px;
    line-height: 1.1;
  }
  .brand-name span { display: block; letter-spacing: 5px; }

  .headline-band {
    position: absolute;
    left: 0; right: 0;
    background: var(--blue);
    color: #fff;
    font-weight: 500;
    text-align: center;
  }

  /* Front */
  .flyer--front .brand-band { top: 18px; height: 78px; }
  .flyer--front .brand-name { font-size: 20px; }
  .flyer--front .brand-name span { font-size: 11px; }
  .flyer--front .headline-band { top: 101px; height: 37px; line-height: 37px; font-size: 18px; }
  .bed-photo {
    position: absolute;
    top: 138px; left: 0; right: 0; height: 187px;
    background: linear-gradient(160deg, var(--photo-light) 0%, #d7e3ea 45%, var(--photo-teal) 75%, #f4f6f8 100%);
  }
  .price-list {
    position: absolute;
    top: 168px; left: 12px; width: 124px;
    list-style: none;
    text-align: right;
    color: var(--navy);
    font-size: 23px;
    font-weight: 500;
    line-height: 34px;
    white-space: nowrap;
    text-shadow: 0 0 4px #fff, 0 0 6px #fff;
  }
  .front-rule { position: absolute; top: 325px; left: 0; right: 0; height: 6px; background: var(--blue); }
  .partner-row {
    position: absolute;
    top: 338px; left: 0; right: 0; height: 40px;
    display: flex; justify-content: center; align-items: center; gap: 12px;
  }
  .partner {
    font-size: 12px; font-weight: 500; color: var(--navy);
    display: flex; align-items: center; gap: 3px;
  }
  .partner i { width: 8px; height: 8px; background: var(--blue); display: inline-block; }
  .partner-badge { width: 28px; height: 28px; background: var(--badge); border-radius: 3px; }
  .front-footer { position: absolute; left: 0; top: 378px; width: 304px; height: 36px; }
  .front-footer-text {
    position: absolute; top: 394px; left: 0; right: 0;
    text-align: center; font-size: 8px; font-weight: 500; color: var(--navy);
  }

  /* Back */
  .flyer--back .brand-band { top: 13px; height: 135px; }
  .flyer--back .brand-name { font-size: 28px; }
  .flyer--back .brand-name span { font-size: 14px; }
  .flyer--back .headline-band { top: 159px; height: 44px; line-height: 44px; font-size: 24px; }
  .map-area {
    position: absolute; top: 213px; left: 10px; width: 284px; height: 110px;
    background: linear-gradient(135deg, var(--map-base), var(--map-road));
  }
  .contact-yellow { position: absolute; top: 331px; left: 0; width: 150px; height: 82px; background: var(--yellow); }
  .call-tag {
    position: absolute; top: 341px; left: 0;
    width: 128px; height: 22px; line-height: 22px;
    background: var(--blue); color: #fff;
    font-size: 14px; font-weight: 500; text-align: center;
    clip-path: polygon(0 0, 100% 0, 92% 100%, 0 100%);
  }
  .phone {
    position: absolute; top: 373px; left: 8px;
    color: var(--navy); font-size: 19px; font-weight: 600;
    white-space: nowrap;
  }
  .address-box {
    position: absolute; top: 333px; left: 136px; width: 168px; height: 80px;
    background: var(--slate);
    clip-path: polygon(9% 0, 100% 0, 100% 100%, 0 100%);
    color: #fff; font-size: 14px; font-weight: 500; font-style: normal;
    line-height: 26px; white-space: nowrap;
    padding: 13px 0 0 22px;
  }
</style>
</head>
<body>

<section class="flyer flyer--front" aria-label="Flyer front">
  <div class="brand-band">
    <p class="brand-name">Bayline Mattress<span>OUTLET</span></p>
  </div>
  <h1 class="headline-band">LOWEST PRICES. BEST BRANDS.</h1>
  <div class="bed-photo" role="img" aria-label="Photo of a made mattress with blue striped and teal pillows"></div>
  <ul class="price-list">
    <li>TWIN - $99</li>
    <li>FULL - $159</li>
    <li>QUEEN - $199</li>
    <li>KING....$299</li>
  </ul>
  <div class="front-rule"></div>
  <div class="partner-row">
    <span class="partner"><i></i>Kaplets</span>
    <span class="partner">Dorvin</span>
    <span class="partner">Norvelle</span>
    <span class="partner-badge" role="img" aria-label="brule &amp; nasher"></span>
  </div>
  <svg class="front-footer" viewBox="0 0 304 36" preserveAspectRatio="none" aria-hidden="true">
    <path d="M0 6 Q152 -4 304 6 L304 36 L0 36 Z" fill="#f2e61c"/>
    <path d="M0 6 Q152 -4 304 6" fill="none" stroke="#0f3f8c" stroke-width="2"/>
  </svg>
  <p class="front-footer-text">AND OTHER GREAT BRAND NAMES!</p>
</section>

<section class="flyer flyer--back" aria-label="Flyer back">
  <div class="brand-band">
    <p class="brand-name">Bayline Mattress<span>OUTLET</span></p>
  </div>
  <h2 class="headline-band">CONTACT US NOW!</h2>
  <div class="map-area" role="img" aria-label="Street map showing the store location"></div>
  <div class="contact-yellow"></div>
  <div class="call-tag">CALL US!</div>
  <p class="phone">(786)471-3926</p>
  <address class="address-box">24315 SW 142ND ST,<br>LAKEMONT, GA 31047, USA</address>
</section>

</body>
</html>
```